SaaS / Consulting / Solution website redesign

We need a website design that:
- Is completely different than our current design : https://plumvessel.net
- Has a very minimal amount of copy
- Changes our positioning from a SaaS application to a solutions company. Solutions company means that we help our customers solve their problems with consulting, training, and tools. An example of a solutions company is here: https://oldpages.example/web/20130111103320/http://www.brindlework.com:80/
- Does not make us look like a start up
- Is more people oriented than technology oriented

We need a designer that:
- Is a rebel at heart
- Is a minimalist
- Tells us why our current site sucks
- Can disagree with us
- Can also do copywriting or already has a copywriter that can help
- Is ok with saying we have capability that we don't in order to see if people actually want that
- Can understand the difference between our grand vision and where we need to focus ourselves today in order to get there

Who we are:
- Entrepreneurs
- Programmers
- Consultants
- Investors

Here's our design goals:
#1 Get customers, investors, employers, and partners excited about our unique and clearly articulated value proposition
#2 Get people to contact us asking for help with their programs
#3 Position ourselves as an expert in the skills based volunteering, mentorship, and group collaboration
#4 Make it easy for people, who already know who we are, to register online

What our grand vision is:
- Create a marketplace where any person can go to our site and find time with anyone they need to meet with. Whether that is their hair stylist, school advisor, parent of your kids class, dentist, attorney, etc.

What will you get if you win:
- In addition to the prize of this project we will have many landing pages and other revisions we will need in the future. We currently don't have a designer or copywriter and need to add that capability to our team

Who do we need to appeal to:
- Directors that are launching innovative programs inside organizations
- IT personnel who are trying to disqualify our technology so they don't have to support it or deal with it when it doesn't go well
- Enterprise IT architects who don't want our product being on its own island within their organization totally incompatible with everything else. Architects which are trying to assess how our platform will co-exist with all their other platforms
- Vice Presidents who want to help their directors understand that we don't have enough experience to help them
- Program managers who have to juggle a million things and need a tool that actually helps instead of confuses them and adds more work for them.
- Program managers & directors that have been given ambiguous goals by their board of directors like "improve retention, increase engagement, create innovation, get people to collaborate." And who have no idea where to start or how to deliver on things like that.
- Program managers, directors, and vice presidents that are trying to understand how our technology and services fit into their existing technology and capability
- Employees who are bored and uninspired with their current tools and are hoping for some excitement in their life. Kind of like candy or a double espresso.
- Investors who think, our company like all the rest, are going to waste their money and make them look like a fool

Other information:
-The CSS and html needs to be responsive

-Our registration onboarding flow needs to collect this information:
User first name
user last name
user email
(verify their email)
user phone number
(verify their phone number)
User profile image (optional)
User profile summary (optional, like a bio, freeform text fiels)
If applicable: Register their organization
Organization name
Organization image (optional)
Account Mailing address
account Billing address (could be same as mailing address)
account Billing email address (could be same as user address)
account Product selection (pricing tier)
account Credit card information

The designs I am getting are a good start but they are only the front page. I just want you to know that I am expecting and need more than a landing page to complete the design. I will likely need a page that outlines the benefits and features of the product itself, how its different than our competitors, which will not be on the front page. I will need a registration flow. I will need a blog page design so we can post blog articles, I will need a team page, a page that goes into detail on our training, our services. I will likely need a page that shows all news and media we have been in. I need to show customer and user quotes, case studies, a way to contact us, partners, general resources like on collaboration, product tutorials, customers. I need the site to address a comprehensive set of needs. I need that design to be consistent and thorough. I know what PlateHarbor is. I'm not using because I need more than a template that was customized. I need to be unique and match our brand thoughtfully, beautifully, and artistically. Someone asked me a question about how Murmly is similar to our tool in the way it is referred by end users and purchased by managers. Our website needs to primarily talk to the managers as I explained in the brief but it needs to appear cool and exciting to our end-users without focusing on the technology too much. Murmly is a tool that teams use to collaborate in small and large enterprises. The value prop for them is that communication is easier. But they don't put that on their website. Why? Because the users of the technology won't go to the website to find out information on it, they get their information from someone who is using it and demos it to them. When Ines tells her manager Otto "Lets get murmly, Ruth is using it at her company and its great" Ines's manager doesn't know anything about murmly so she promptly googles it. The most important thing from Ines's perspective is that Otto agrees to try it out. Otto's biggest concern is that productivity will be enhanced to degraded. Murmly knows this and so on the front page they know they are talking to Otto NOT Ines because Ines is already sold on it and doesn't need to get sold on the website. Ines is end user. Otto is the purchaser. We have the same problem and so our end users are not the ones purchasing our product, their managers are purchasing our product. We get referred by our end users and vetted by their managers. Hope this helps! Thank you for looking at this project!  Added Wednesday, June 7, 2017

Another observation I am having about the designs being submitted. I believe we used the animations on our current website because animations / cartoons connect with the "inner child" in our users. Whatever that means :-). I think it's what makes our brand fun. I have a hard time imagining that we could make the design fun looking without animations but I'm sure it can be achieved. I also recognize that blending pictures of real people and animations is hard. So either we must masterfully blend them, use only animations, or make the real people have a LOT of fun! So far most of the designs while achieve the goal of appealing to the serious Vice Presidents and directors, they are not doing a good job at appealing to the overworked program managers and bored employees. There seems to stand another challenge with animations which is animations are hard to find and/or create that achieve the message / emotion we are trying to communicate. I don't have any good answers for this but I will say we can hire both animators and illustrators if we need to. All you have to do is communicate the effect in the website design with some simpler version maybe not the end illustration or animation itself. Added Wednesday, June 7, 2017

• Sex appeal and a sense of humor. Copy that makes people excited and clairvoyant about our potential.
• Boring renditions of other non-inspiring websites

```html
<!DOCTYPE html>
<html lang="en">
<head>
<meta charset="utf-8">
<title>Plumvessel</title>
<link href="https://fonts.googleapis.com/css2?family=Didact+Gothic&family=Open+Sans:wght@400;600;700&display=swap" rel="stylesheet">
<style>
:root{
  --gold:#f4c20d;
  --blue:#3aa8dc;
  --btn:#3ab0e4;
  --ink:#2d2e3b;
  --text:#333;
  --green:#8bcf7e;
  --red:#f2625e;
  --yellow:#fde068;
  --card-light:#e8e8e8;
  --panel:#f2f2f2;
  --footer:#efefef;
  --footer-bar:#e0e0e0;
}
*{margin:0;padding:0;box-sizing:border-box}
html,body{width:686px;height:1200px;overflow:hidden;background:#fff}
body{position:relative;font-family:"Open Sans",sans-serif;color:var(--text)}
.abs{position:absolute}
.hero{left:0;top:0;width:686px;height:310px;background:linear-gradient(100deg,#3c3a3c 0%,#6d6560 30%,#9a8f86 55%,#c9bfb6 75%,#8a7f78 100%)}
.hero-shade{left:0;top:0;width:686px;height:310px;background:linear-gradient(90deg,rgba(30,30,40,.55),rgba(30,30,40,.1) 60%,rgba(0,0,0,0))}
.logo{left:57px;top:8px;font-family:"Didact Gothic",sans-serif;font-size:19px;color:var(--gold)}
.nav{top:18px;font-family:"Didact Gothic",sans-serif;font-size:8px;letter-spacing:-.1px;white-space:nowrap;color:var(--gold)}
.nav-active{left:330px;top:0;width:32px;height:2px;background:var(--gold)}
.hero-title{left:57px;top:97px;width:270px;font-size:13.5px;line-height:16.5px;font-weight:400;color:var(--gold)}
.btn{background:var(--btn);color:#fff;font-size:7.5px;font-weight:700;text-align:center;letter-spacing:.3px}
.hero-btn{left:57px;top:164px;width:70px;height:18px;line-height:18px}
.arrows{left:57px;top:210px}
.section-title{left:0;width:686px;text-align:center;font-family:"Didact Gothic",sans-serif;font-size:24px;font-weight:400;color:var(--blue)}
.subtitle{left:0;top:353px;width:686px;text-align:center;font-size:12px;color:#222}
.intro{left:86px;top:387px;width:514px;font-size:6.8px;line-height:11.6px;text-align:center;color:#222}
.read-btn{left:309px;top:442px;width:69px;height:18px;line-height:18px}
.pillar{top:480px;width:134px;height:101px;text-align:center;padding-top:24px}
.pillar h3{font-size:7.5px;font-weight:700;color:#222;margin-bottom:8px}
.pillar p{font-size:6.5px;line-height:11.5px;width:104px;margin:0 auto;color:#333}
.pillar.how h3,.pillar.how p{color:#fff}
.pillar svg{position:absolute;left:62px;top:80px}
.role{top:651px;width:137px;height:105px;text-align:center;border-top:4px solid}
.role.light{background:var(--card-light);color:#222}
.role.dark{background:var(--ink);color:#fff}
.role svg{position:absolute;left:0;right:0;margin:auto;top:18px}
.role span{position:absolute;left:0;width:100%;top:74px;font-size:9px;font-weight:600}
.tabs{left:96px;top:830px;width:126px}
.tab{height:23.5px;line-height:23.5px;padding-left:11px;font-size:9px;color:#333;white-space:nowrap}
.tab.active{background:var(--ink);color:var(--gold);position:relative}
.tab.active::after{content:"";position:absolute;right:-6px;top:6px;border-left:6px solid var(--gold);border-top:6px solid transparent;border-bottom:6px solid transparent}
.tab-panel{left:222px;top:830px;width:369px;height:157px;background:var(--panel);border-left:2px solid var(--gold)}
.tab-panel h4{position:absolute;left:17px;top:12px;font-size:12px;font-weight:700;color:#222}
.tab-panel ul{position:absolute;left:17px;top:36px;list-style:none}
.tab-panel li{font-size:7.5px;height:17.6px;color:#333}
.tab-panel li::before{content:"\2192";color:#888;margin-right:10px}
.tab-photo{left:198px;top:10px;width:162px;height:141px;background:linear-gradient(160deg,#dbe8f2 0%,#9fb9cc 40%,#5f7a90 75%,#b09a70 100%)}
.footer{left:0;top:1007px;width:686px;height:175px;background:var(--footer)}
.footer-bar{left:0;top:1182px;width:686px;height:18px;background:var(--footer-bar);text-align:center;font-size:6.5px;line-height:18px;color:#333}
.f-head{top:1028px;font-size:12px;font-weight:400;color:#222}
.links{left:86px;top:1054px;list-style:none}
.links li{font-size:6.8px;height:14.6px;color:#333}
.links li::before{content:"\203A";margin-right:9px}
.bubble{left:199px;top:1052px;width:126px;height:76px;background:#e2e2e2;border-radius:6px;padding:8px 9px;font-size:6.5px;line-height:12px;text-align:justify;color:#444}
.bubble::after{content:"";position:absolute;left:14px;bottom:-7px;border-top:7px solid #e2e2e2;border-right:7px solid transparent}
.avatar{left:218px;top:1134px;width:27px;height:27px;border-radius:50%;background:#b89a80}
.person{left:253px;top:1139px;font-size:7.5px;line-height:9px;color:#333}
.contact{left:366px;font-size:6.8px;color:#333}
.contact svg{position:absolute;left:0;top:0}
.contact span{position:absolute;left:15px;top:0;white-space:nowrap}
.social{left:520px;font-size:6.8px;color:#333}
.social i{position:absolute;left:0;top:-4px;width:15px;height:15px}
.social span{position:absolute;left:25px;top:0;white-space:nowrap}
</style>
</head>
<body>

<header>
  <div class="abs hero" role="img" aria-label="Photo of a smiling shop worker with an orange scarf in a busy café"></div>
  <div class="abs hero-shade"></div>
  <div class="abs logo">Plumvessel</div>
  <div class="abs nav-active"></div>
  <nav>
    <a class="abs nav" style="left:335px">Home</a>
    <a class="abs nav" style="left:375px">About</a>
    <a class="abs nav" style="left:415px">Services</a>
    <a class="abs nav" style="left:465px">Solutions</a>
    <a class="abs nav" style="left:517px">Testimonials</a>
    <a class="abs nav" style="left:579px">Contact Us</a>
  </nav>
  <h1 class="abs hero-title">We help your people meet, mentor and work together with consulting, training, and tools.</h1>
  <div class="abs btn hero-btn">LEARN MORE</div>
  <svg class="abs arrows" width="30" height="12" viewBox="0 0 30 12"><path d="M6 1 L1 6 L6 11 M22 1 L27 6 L22 11" fill="none" stroke="#fff" stroke-width="1.6"/></svg>
</header>

<section class="vision">
  <h2 class="abs section-title" style="top:322px">The Plumvessel Vision</h2>
  <p class="abs subtitle">How we’re going to change the world by connecting people in-person</p>
  <p class="abs intro">We design the programs, train the people and bring the tools that make mentoring, volunteering and collaboration actually happen.<br>Your teams get time together. Your leaders get results they can measure.</p>
  <div class="abs btn read-btn">READ MORE</div>

  <div class="abs pillar" style="left:119px;background:var(--green)">
    <h3>WHAT</h3><p>We help organisations connect people in person</p>
    <svg width="9" height="9" viewBox="0 0 10 10"><circle cx="5" cy="5" r="5" fill="#222"/><path d="M3 5h4M5.3 3l2 2-2 2" stroke="#fff" fill="none" stroke-width="1.2"/></svg>
  </div>
  <div class="abs pillar how" style="left:276px;background:var(--red)">
    <h3>HOW</h3><p>Consulting, training and tools built around people</p>
    <svg width="9" height="9" viewBox="0 0 10 10"><circle cx="5" cy="5" r="5" fill="#fff"/><path d="M3 5h4M5.3 3l2 2-2 2" stroke="#f2625e" fill="none" stroke-width="1.2"/></svg>
  </div>
  <div class="abs pillar" style="left:433px;background:var(--yellow)">
    <h3>WHY</h3><p>People are becoming more isolated than connected because of technology</p>
    <svg width="9" height="9" viewBox="0 0 10 10"><circle cx="5" cy="5" r="5" fill="#222"/><path d="M3 5h4M5.3 3l2 2-2 2" stroke="#fff" fill="none" stroke-width="1.2"/></svg>
  </div>
</section>

<section class="team">
  <h2 class="abs section-title" style="top:608px">Who We are ?</h2>
  <div class="abs role light" style="left:57px;border-color:var(--red)">
    <svg width="44" height="52" viewBox="0 0 44 52"><circle cx="22" cy="13" r="11" fill="#2d2e3b"/><path d="M2 52 Q2 30 22 28 Q42 30 42 52Z" fill="#2d2e3b"/><path d="M19 30 L22 34 L25 30 L23.5 46 L22 48 L20.5 46Z" fill="#fff"/></svg>
    <span>Entrepreneurs</span>
  </div>
  <div class="abs role dark" style="left:202px;border-color:var(--blue)">
    <svg width="44" height="52" viewBox="0 0 44 52"><path d="M10 22 Q8 2 22 2 Q36 2 34 22 Z" fill="#fff"/><circle cx="22" cy="15" r="9" fill="#2d2e3b"/><path d="M2 52 Q2 30 22 28 Q42 30 42 52Z" fill="#fff"/><path d="M16 40l-3 3 3 3M28 40l3 3-3 3M24 38l-4 10" stroke="#2d2e3b" stroke-width="1.6" fill="none"/></svg>
    <span>Programmers</span>
  </div>
  <div class="abs role light" style="left:347px;border-color:var(--yellow)">
    <svg width="80" height="52" viewBox="0 0 80 52"><circle cx="17" cy="16" r="8" fill="#2d2e3b"/><circle cx="63" cy="16" r="8" fill="#2d2e3b"/><path d="M0 46 Q0 27 17 26 Q34 27 34 46Z M46 46 Q46 27 63 26 Q80 27 80 46Z" fill="#2d2e3b"/><circle cx="40" cy="12" r="10" stroke="#e8e8e8" stroke-width="2" fill="#2d2e3b"/><path d="M20 52 Q20 27 40 25 Q60 27 60 52Z" stroke="#e8e8e8" stroke-width="2" fill="#2d2e3b"/></svg>
    <span>Consultants</span>
  </div>
  <div class="abs role dark" style="left:493px;border-color:var(--green)">
    <svg width="50" height="52" viewBox="0 0 50 52"><circle cx="20" cy="13" r="11" fill="#fff"/><path d="M0 46 Q0 28 20 27 Q34 28 38 36 L38 46Z" fill="#fff"/><text x="34" y="50" font-size="22" font-weight="700" fill="#fff" font-family="Open Sans,sans-serif">$</text></svg>
    <span>Investors</span>
  </div>
</section>

<section class="cases">
  <h2 class="abs section-title" style="top:777px">Business Case</h2>
  <div class="abs tabs">
    <div class="tab active">Volunteer coordination</div>
    <div class="tab">Office hours</div>
    <div class="tab">Mentor programs</div>
    <div class="tab">Post-event networking</div>
    <div class="tab">Professional services</div>
    <div class="tab">Traveling networking</div>
  </div>
  <div class="abs tab-panel">
    <h4>Volunteer coordination</h4>
    <ul>
      <li>HR/Enterprise</li>
      <li>Local Government</li>
      <li>Churches</li>
      <li>University</li>
      <li>Non-profits</li>
    </ul>
    <div class="abs tab-photo" role="img" aria-label="Photo of a businessman looking up at glass office towers"></div>
  </div>
</section>

<footer>
  <div class="abs footer"></div>
  <h5 class="abs f-head" style="left:86px">Quick Links</h5>
  <ul class="abs links">
    <li>Home</li><li>About</li><li>Services</li><li>Solutions</li><li>Testimonials</li><li>Contact Us</li>
  </ul>

  <h5 class="abs f-head" style="left:203px;letter-spacing:.4px">Testimonials</h5>
  <div class="abs bubble">“Lorem ipsum dolor sit amet, consectetur adipiscing elit, sed do eiusmod tempor incididunt ut labore et dolore magna aliqua. Ut enim ad minim veniam.”</div>
  <div class="abs avatar" role="img" aria-label="Portrait photo of the reviewer"></div>
  <div class="abs person">Lee Marsh,<br>Lorium ipsum</div>

  <h5 class="abs f-head" style="left:366px">Contact Us</h5>
  <div class="abs contact" style="top:1057px"><svg width="8" height="10" viewBox="0 0 8 10"><path d="M4 10 L1 5 A3.4 3.4 0 1 1 7 5Z" fill="#222"/><circle cx="4" cy="3.6" r="1.3" fill="#fff"/></svg><span>PO Box 4410, Tarrow, NSW, 2199</span></div>
  <div class="abs contact" style="top:1077px"><svg width="8" height="8" viewBox="0 0 8 8"><path d="M1 0h2l1 2-1.2 1A5 5 0 0 0 5 5.2L6 4l2 1v2c0 .6-.5 1-1 1A7 7 0 0 1 0 1c0-.6.4-1 1-1Z" fill="#222"/></svg><span>0400 555 018</span></div>
  <div class="abs contact" style="top:1092px"><svg width="7" height="9" viewBox="0 0 7 9"><rect x=".5" y=".5" width="6" height="8" fill="none" stroke="#222"/><path d="M2 2.5h3M2 4.5h3M2 6.5h3" stroke="#222"/></svg><span>Business Address</span></div>
  <div class="abs contact" style="top:1109px;left:381px;line-height:12px">Suite 3.05, 12 Marlo Avenue,<br>Tarrow NSW 2199</div>
  <div class="abs contact" style="top:1139px"><svg width="8" height="6" viewBox="0 0 8 6"><rect width="8" height="6" fill="#222"/><path d="M0 0l4 3 4-3" stroke="#fff" fill="none" stroke-width=".8"/></svg><span>hello@plumvessel.net</span></div>

  <h5 class="abs f-head" style="left:519px">Follow Us</h5>
  <div class="abs social" style="top:1055px"><i style="background:#3b5a9a"></i><span>Friendlane</span></div>
  <div class="abs social" style="top:1077px"><i style="background:#29aae1"></i><span>Chirpline</span></div>
  <div class="abs social" style="top:1098px"><i style="background:#cb2027"></i><span>Pinwheel</span></div>
  <div class="abs social" style="top:1118px"><i style="background:#b86a2c"></i><span>Lenscape</span></div>

  <div class="abs footer-bar">Copyrights © 2017 - All Rights Reserved</div>
</footer>

</body>
</html>
```